** Wanted ** Wordpress web design for scaffolding rental and construction company

We need a website design and must be functional to show a basic overview of what our company offers as a service. We have a domain name and a logo but we need web design. This web site should have another scaffolding rental page for construction and renovation as well as a quote section where customers can enter their personal information and also upload photos. The site% 26quot; www.brindlework.com% 26quot; should be intuitive, clear and classy ... The logo must be found on the site in several ways.

Target Market(s)

Professional and no professional

Coding

Coded - Design and coding required

Number of Pages Required

3 page

Font styles to use
Serif
Sans Serif
Decorative
Script

Requirements
Must have
• Our logo
Nice to have
• Slogan:% 26quot; The height% 26 # 224; port% 26 # 233; e hand% 26quot;

```html
<!DOCTYPE html>
<html lang="en">
<head>
<meta charset="utf-8">
<title>Brindlework – Scaffolding &amp; Construction</title>
<link rel="stylesheet" href="https://fonts.googleapis.com/css2?family=Poppins:ital,wght@0,300;0,400;0,500;0,600;1,300&family=Fredoka:wght@600&family=Lobster&display=swap">
<style>
:root{
  --orange:#f7811f;
  --peach:#fbd5b5;
  --dark:#262626;
  --dark-2:#333333;
  --ink:#222222;
  --muted:#6b6b6b;
  --light:#f6f6f6;
  --white:#ffffff;
}
*{margin:0;padding:0;box-sizing:border-box}
html,body{width:1200px;height:3578px;overflow:hidden}
body{position:relative;background:var(--white);font-family:"Poppins",sans-serif;color:var(--ink)}
.abs{position:absolute}
.heading{font-family:"Fredoka",sans-serif;font-weight:600;color:var(--orange)}

/* hero */
.hero{left:0;top:0;width:1200px;height:600px;background:linear-gradient(135deg,#5a5550 0%,#3d3b3a 45%,#6a645c 100%)}
.hero-shape{left:0;top:0}
.brand{display:flex;align-items:center;gap:8px;font-family:"Poppins",sans-serif;font-weight:600;font-size:19px;color:var(--orange);letter-spacing:1px;text-transform:uppercase}
.brand-mark{width:14px;height:14px;background:var(--orange)}
.nav{top:21px;font-size:12.5px;color:var(--white)}
.nav a{position:absolute;color:var(--white);text-decoration:none;white-space:nowrap}
.nav a.active{color:var(--orange)}
.hero-title{left:0;width:1200px;top:205px;text-align:center;font-family:"Lobster",cursive;font-size:58px;color:var(--white)}
.hero-text{left:300px;width:600px;top:292px;text-align:center;font-size:12.5px;line-height:22px;color:var(--white)}
.btn{display:flex;align-items:center;justify-content:center;border:4px solid var(--orange);font-size:13.5px;color:var(--white);text-decoration:none}
.dots{left:1114px;top:251px;display:flex;flex-direction:column;gap:9px}
.dots span{width:12px;height:12px;border:1.5px solid var(--orange);border-radius:50%}
.dots span.on{background:var(--orange)}

/* welcome */
.worker{left:160px;top:570px;width:298px;height:423px;background:linear-gradient(180deg,#e9c54a 0%,#7ea1c2 40%,#b78a4a 100%);border-radius:40px 40px 0 0}
.welcome-title{left:590px;top:668px;font-size:32px}
.body-text{font-size:12px;line-height:22.5px;color:var(--muted)}
.welcome-text{left:590px;top:729px;width:455px}
.btn-dark{color:var(--ink)}

/* services */
.services{left:0;top:993px;width:1200px;height:532px;background:linear-gradient(135deg,#3a3633 0%,#5b5048 50%,#2e2c2b 100%)}
.services-title{left:0;width:1200px;top:1033px;text-align:center;font-size:32px;color:var(--white)}
.card{top:1103px;width:262px;height:276px;background:var(--white);border-radius:3px;text-align:center}
.card-icon{position:absolute;left:96px;top:20px}
.card h3{position:absolute;left:0;width:100%;top:136px;font-weight:400;font-size:16px;letter-spacing:.3px}
.card p{position:absolute;left:22px;width:218px;top:163px;font-size:11.5px;line-height:22px;color:var(--muted)}
.card a{position:absolute;left:0;width:100%;top:240px;font-size:11.5px;font-weight:600;color:var(--orange);text-decoration:none}

/* testimonial */
.testi-title{left:162px;top:1657px;font-size:32px}
.quote-mark{left:160px;top:1712px;font-family:"Lobster",cursive;font-size:90px;color:#e6e6e6;line-height:1}
.quote{left:162px;top:1733px;width:360px;font-size:12px;line-height:22.5px;font-style:italic;font-weight:300;color:var(--ink)}
.client-name{left:162px;top:1815px;font-size:16px}
.client-role{left:162px;top:1842px;font-size:11px;color:var(--muted)}
.avatar{left:159px;top:1884px;width:74px;height:74px;border-radius:50%;background:linear-gradient(160deg,#d9e3ea,#9fb6c8);box-shadow:0 0 0 3px #eee}
.portrait{left:721px;top:1681px;width:258px;height:258px;border-radius:50%;background:linear-gradient(160deg,#c9dceb 0%,#7fa2bf 60%,#d8d2cc 100%)}

/* gallery */
.gallery{left:0;top:2084px;width:1200px;height:586px;background:var(--light)}
.gallery-title{left:0;width:1200px;top:2115px;text-align:center;font-size:32px;text-transform:uppercase;letter-spacing:1px}
.photo{position:absolute}

/* contact */
.contact-title{left:0;width:1200px;top:2737px;text-align:center;font-size:32px}
.field{border-bottom:1px solid #d8d8d8;font-size:11px;color:var(--muted);padding-bottom:6px}

/* footer */
.footer{left:0;top:3150px;width:1200px;height:428px}
.foot-title{font-family:"Fredoka",sans-serif;font-weight:600;font-size:22px;color:var(--white)}
.foot-text{font-size:12px;line-height:22.5px;color:var(--white)}
.foot-links{list-style:none;font-size:12px;color:var(--white)}
.foot-links li{height:27px;display:flex;align-items:center;gap:8px}
.foot-links li::before{content:"";width:5px;height:5px;border-right:1.2px solid var(--orange);border-top:1.2px solid var(--orange);transform:rotate(45deg)}
.contact-line{display:flex;gap:12px;font-size:12px;line-height:19px;color:var(--white)}
.social{width:37px;height:37px;border-radius:50%;background:var(--orange)}
.copy-rule{left:0;top:3535px;width:1200px;height:1px;background:#555}
.copy{left:0;width:1200px;top:3551px;text-align:center;font-size:11px;color:var(--white)}
</style>
</head>
<body>

<!-- hero -->
<div class="abs hero" role="img" aria-label="Photo of workers assembling yellow scaffolding"></div>
<svg class="abs hero-shape" width="1200" height="620" viewBox="0 0 1200 620" aria-hidden="true">
  <polygon points="0,479 600,600 1200,479 1200,620 0,620" fill="#ffffff"/>
  <rect x="593" y="542" width="14" height="30" rx="7" fill="none" stroke="#333" stroke-width="1.6"/>
  <line x1="600" y1="550" x2="600" y2="557" stroke="#333" stroke-width="1.6"/>
</svg>
<div class="abs brand" style="left:162px;top:32px"><span class="brand-mark"></span>Brindlework</div>
<nav class="abs nav" style="left:0;top:21px;width:1200px">
  <a class="active" style="left:639px">Home</a>
  <a style="left:697px">About</a>
  <a style="left:756px">Services</a>
  <a style="left:828px">Testimonials</a>
  <a style="left:926px">Gallery</a>
  <a style="left:990px">Contact</a>
</nav>
<h1 class="abs hero-title">The height; port</h1>
<p class="abs hero-text">Lorem Ipsum is simply dummy text of the printing and typesetting industry. Lorem Ipsum has been the industry's standard dummy text ever since the 1500s.</p>
<a class="abs btn" style="left:525px;top:364px;width:149px;height:51px">Learn More</a>
<div class="abs dots"><span></span><span></span><span class="on"></span><span></span><span></span></div>

<!-- welcome -->
<div class="abs worker" role="img" aria-label="Photo of a female site worker in a hard hat holding a clipboard"></div>
<h2 class="abs heading welcome-title">Welcome To Brindlework</h2>
<p class="abs body-text welcome-text">Lorem Ipsum is simply dummy text of the printing and typesetting industry. Lorem Ipsum has been the industry's standard dummy text ever since the 1500s. Lorem Ipsum is simply dummy text of the printing and typesetting industry. Lorem Ipsum has been the industry's standard dummy text ever since the 1500s.</p>
<a class="abs btn btn-dark" style="left:590px;top:865px;width:149px;height:52px">Learn More</a>
<svg class="abs" style="left:655px;top:863px" width="20" height="10" aria-hidden="true"><polygon points="0,0 20,0 10,9" fill="#fff"/></svg>

<!-- services -->
<div class="abs services" role="img" aria-label="Background photo of a construction site"></div>
<svg class="abs" style="left:0;top:1400px" width="1200" height="130" viewBox="0 0 1200 130" aria-hidden="true">
  <polygon points="0,3 600,125 1200,3 1200,130 0,130" fill="#ffffff"/>
  <polyline points="588,74 600,84 612,74" fill="none" stroke="#bbb" stroke-width="1.3"/>
  <polyline points="588,79 600,89 612,79" fill="none" stroke="#bbb" stroke-width="1.3"/>
</svg>
<h2 class="abs heading services-title">Our Services</h2>

<div class="abs card" style="left:162px">
  <svg class="card-icon" width="90" height="90" viewBox="0 0 90 90" aria-hidden="true">
    <polygon points="45,0 90,45 45,90 0,45" fill="var(--peach)" transform="translate(20,0) scale(.8)"/>
    <g fill="none" stroke="#333" stroke-width="1.6"><rect x="10" y="24" width="58" height="46"/><line x1="29" y1="24" x2="29" y2="70"/><line x1="49" y1="24" x2="49" y2="70"/><line x1="10" y1="47" x2="68" y2="47"/><line x1="10" y1="24" x2="29" y2="47"/><line x1="49" y1="47" x2="68" y2="70"/></g>
  </svg>
  <h3>SCAFFOLDING</h3>
  <p>Lorem Ipsum is simply dummy text of the printing and typesetting industry.</p>
  <a>Learn More ▸</a>
</div>
<div class="abs card" style="left:469px">
  <svg class="card-icon" width="90" height="90" viewBox="0 0 90 90" aria-hidden="true">
    <polygon points="45,0 90,45 45,90 0,45" fill="var(--peach)" transform="translate(20,0) scale(.8)"/>
    <g fill="none" stroke="#333" stroke-width="1.6"><rect x="12" y="26" width="54" height="40"/><line x1="12" y1="58" x2="66" y2="58"/><rect x="24" y="34" width="16" height="16"/><rect x="44" y="30" width="14" height="22"/></g>
  </svg>
  <h3>ELEVATION</h3>
  <p>Lorem Ipsum is simply dummy text of the printing and typesetting industry.</p>
  <a>Learn More ▸</a>
</div>
<div class="abs card" style="left:776px">
  <svg class="card-icon" width="90" height="90" viewBox="0 0 90 90" aria-hidden="true">
    <polygon points="45,0 90,45 45,90 0,45" fill="var(--peach)" transform="translate(20,0) scale(.8)"/>
    <g fill="none" stroke="#333" stroke-width="1.6"><polyline points="14,40 38,20 62,40"/><rect x="20" y="38" width="36" height="26"/><rect x="30" y="44" width="16" height="14"/><line x1="38" y1="44" x2="38" y2="58"/><line x1="10" y1="70" x2="66" y2="70"/></g>
  </svg>
  <h3>RENOVATION</h3>
  <p>Lorem Ipsum is simply dummy text of the printing and typesetting industry.</p>
  <a>Learn More ▸</a>
</div>

<!-- testimonial -->
<h2 class="abs heading testi-title">Testimonial</h2>
<div class="abs quote-mark" aria-hidden="true">“</div>
<p class="abs quote">Lorem Ipsum is simply dummy text of the printing and typesetting industry. Lorem Ipsum has been the industry's standard dummy text ever since the 1500s</p>
<p class="abs client-name">Client Name</p>
<p class="abs client-role">Lorem Ipsum</p>
<div class="abs avatar" role="img" aria-label="Client portrait thumbnail"></div>
<svg class="abs" style="left:681px;top:1604px" width="358" height="403" viewBox="0 0 358 403" aria-hidden="true">
  <path d="M225,8 C275,-15 320,40 345,95 C370,155 350,230 300,240 C260,330 220,395 175,402 C120,410 60,360 25,320 C-10,280 -5,230 40,180 C90,150 140,70 225,8 Z" fill="#000"/>
</svg>
<div class="abs portrait" role="img" aria-label="Photo of a smiling businesswoman at a desk"></div>

<!-- gallery -->
<div class="abs gallery"></div>
<h2 class="abs heading gallery-title">Our Gallery</h2>
<div class="photo" style="left:162px;top:2182px;width:449px;height:450px;background:linear-gradient(160deg,#7f9eb9 0%,#2f3c62 50%,#4a7a3a 100%)" role="img" aria-label="Photo of a modern apartment building"></div>
<div class="photo" style="left:626px;top:2182px;width:413px;height:225px;background:linear-gradient(135deg,#5b88b0 0%,#e98b3a 55%,#d3c7b0 100%)" role="img" aria-label="Photo of engineers in orange safety vests and hard hats"></div>
<div class="photo" style="left:626px;top:2424px;width:199px;height:208px;background:linear-gradient(180deg,#3d76c0 0%,#b3c5d6 60%,#a77b54 100%)" role="img" aria-label="Photo of a roofer working on timber rafters"></div>
<div class="photo" style="left:840px;top:2424px;width:199px;height:208px;background:linear-gradient(135deg,#f4c277 0%,#e09a3d 50%,#2a2016 100%)" role="img" aria-label="Silhouette photo of a worker on steel scaffolding at sunset"></div>

<!-- contact -->
<h2 class="abs heading contact-title">Contact Us</h2>
<form>
  <div class="abs field" style="left:312px;top:2818px;width:262px">First Name</div>
  <div class="abs field" style="left:624px;top:2818px;width:262px">Last Name</div>
  <div class="abs field" style="left:312px;top:2869px;width:262px">Phone</div>
  <div class="abs field" style="left:624px;top:2869px;width:262px">E-mail</div>
  <div class="abs field" style="left:312px;top:2921px;width:574px">Message</div>
  <a class="abs btn btn-dark" style="left:525px;top:2963px;width:149px;height:51px">SEND</a>
</form>

<!-- footer -->
<div class="abs footer" role="img" aria-label="Dark photo of cranes and a building under construction"
     style="background:linear-gradient(180deg,#2f2f2f,#1f1f1f);clip-path:polygon(0 114px,600px 0,1200px 114px,1200px 100%,0 100%)"></div>
<div class="abs brand" style="left:162px;top:3319px"><span class="brand-mark"></span>Brindlework</div>
<p class="abs foot-text" style="left:162px;top:3378px;width:200px">Lorem Ipsum is simply dummy text of the printing and typesetting industry. Lorem Ipsum has been the industry's...</p>

<h3 class="abs foot-title" style="left:431px;top:3280px">Site Map</h3>
<ul class="abs foot-links" style="left:434px;top:3335px">
  <li>Home</li><li>About</li><li>Services</li><li>Gallery</li><li>Testimonial</li><li>Contact</li>
</ul>

<h3 class="abs foot-title" style="left:613px;top:3280px">Contact Us</h3>
<div class="abs contact-line" style="left:613px;top:3344px;width:180px">
  <svg width="16" height="20" viewBox="0 0 16 20" aria-hidden="true"><path d="M8,1 C4,1 1.5,4 1.5,7.5 C1.5,12 8,19 8,19 C8,19 14.5,12 14.5,7.5 C14.5,4 12,1 8,1 Z" fill="none" stroke="var(--orange)" stroke-width="1.8"/><circle cx="8" cy="7.5" r="2.3" fill="var(--orange)"/></svg>
  <span>123 - Lorem ipsum is dummy text and dynem.</span>
</div>
<div class="abs contact-line" style="left:613px;top:3398px">
  <svg width="16" height="18" viewBox="0 0 16 18" aria-hidden="true"><path d="M3,1 L6,1 L7,5 L5,7 C6,10 8,12 11,13 L13,11 L16,12 L16,15 C16,16 15,17 14,17 C7,16 1,10 1,3 C1,2 2,1 3,1 Z" fill="var(--orange)"/></svg>
  <span>(+91) 555 014 2368</span>
</div>
<div class="abs contact-line" style="left:613px;top:3440px">
  <svg width="18" height="16" viewBox="0 0 18 16" aria-hidden="true"><path d="M1,6 L9,1 L17,6 L17,15 L1,15 Z M1,6 L9,11 L17,6" fill="none" stroke="var(--orange)" stroke-width="1.6"/></svg>
  <span>info@brindlework.com</span>
</div>

<h3 class="abs foot-title" style="left:861px;top:3280px">Follow Us</h3>
<div class="abs" style="left:862px;top:3346px;display:flex;gap:10px">
  <span class="social" role="img" aria-label="Social profile link"></span>
  <span class="social" role="img" aria-label="Social profile link"></span>
  <span class="social" role="img" aria-label="Social profile link"></span>
  <span class="social" role="img" aria-label="Social profile link"></span>
</div>

<div class="abs copy-rule"></div>
<p class="abs copy">©BRINDLEWORK - 2020 All Rights Reserved.</p>

</body>
</html>
```